Looking for a modern, Professional business card design

We have a simple business card, but are looking for a more modern, professional look. A sample of the basic card is attached as well as the logo. We would also like to add that we offer:
Struggling with your finances?
- Learn to become debt free
- Discover the power of cash
- Control your money instead of it controlling you
Let us help you achieve a new level of financial freedom!
Also, we would like to have a "SPECIAL OFFER!: FREE 30 minute consultation"
Financial Planning

```html
<!DOCTYPE html>
<html lang="en">
<head>
<meta charset="utf-8">
<title>Clearpath Financial Coaching – Business Card</title>
<link href="https://fonts.googleapis.com/css2?family=Arimo:wght@400;700&family=Archivo+Black&display=swap" rel="stylesheet">
<style>
  :root {
    --backdrop: #9b9b9b;
    --paper: #ecedef;
    --ink-black: #0c0c0c;
    --ink-dark: #2b2b2b;
    --ink-body: #3a3a3a;
    --brand-green: #2e9a3e;
    --brand-green-light: #7cc242;
    --white: #ffffff;
  }
  * { box-sizing: border-box; margin: 0; padding: 0; }
  html, body {
    width: 1105px; height: 1200px; overflow: hidden;
    background: var(--backdrop);
    font-family: "Arimo", Arial, sans-serif;
  }
  .canvas { position: relative; width: 1105px; height: 1200px; }
  .card {
    position: absolute; left: 182px; width: 746px; height: 427px;
    background: var(--paper); overflow: hidden;
  }
  .card--front { top: 119px; }
  .card--back { top: 637px; }
  .card__art { position: absolute; inset: 0; }

  .brand {
    position: absolute; display: flex; align-items: center; gap: 14px;
    font-family: "Arimo", Arial, sans-serif; font-weight: 700;
    letter-spacing: 0.5px; line-height: 1.15;
  }
  .brand__dot { width: 22px; height: 22px; border-radius: 50%; background: var(--brand-green-light); flex: none; }
  .brand__name { display: block; }
  .brand--front { left: 44px; top: 80px; font-size: 29px; color: var(--white); }
  .brand--back { left: 0; right: 0; top: 80px; justify-content: center; font-size: 36px; color: var(--ink-black); }
  .brand--back .brand__dot { width: 26px; height: 26px; }

  .contact { position: absolute; right: 36px; top: 236px; text-align: right; }
  .contact__name { font-size: 31px; font-weight: 400; color: var(--brand-green); letter-spacing: 0.5px; }
  .contact__title { margin-top: 8px; font-size: 20px; color: var(--ink-dark); }
  .contact__list { list-style: none; margin-top: 18px; }
  .contact__item {
    display: flex; justify-content: flex-end; align-items: center; gap: 12px;
    font-size: 19px; color: var(--ink-body); line-height: 29px;
  }
  .contact__icon { width: 18px; height: 18px; flex: none; }

  .pitch { position: absolute; left: 0; right: 0; top: 250px; text-align: center; }
  .pitch__headline { font-size: 20px; font-weight: 700; color: var(--brand-green); letter-spacing: 0.3px; }
  .pitch__line { font-size: 19px; color: var(--ink-body); line-height: 27px; }
  .pitch__line:first-of-type { margin-top: 6px; }
  .pitch__bullet { display: inline-block; width: 8px; height: 8px; border-radius: 50%; background: var(--brand-green); margin: 0 6px 2px 4px; vertical-align: middle; }
  .pitch__closing { font-size: 18px; font-weight: 700; color: var(--ink-black); line-height: 26px; }
  .pitch__rule { width: 552px; height: 2px; background: var(--brand-green); margin: 8px auto 0; }
  .pitch__offer {
    margin-top: 8px; font-family: "Archivo Black", "Arial Black", sans-serif;
    font-size: 25px; color: var(--brand-green-light); letter-spacing: 0.3px;
  }
</style>
</head>
<body>
<main class="canvas">

  <section class="card card--front" aria-label="Card front">
    <svg class="card__art" viewBox="0 0 746 427" aria-hidden="true">
      <path d="M0,0 H640 C540,15 470,80 420,160 C360,255 240,300 0,285 Z" fill="var(--ink-black)"/>
      <path d="M0,265 C170,300 300,285 380,225 C320,300 190,335 0,320 Z" fill="var(--brand-green)"/>
      <path d="M480,135 C560,80 650,55 746,52 V92 C650,90 560,105 480,135 Z" fill="var(--brand-green)"/>
    </svg>
    <div class="brand brand--front"><span class="brand__dot"></span><span class="brand__name">CLEARPATH<br>FINANCIAL COACHING</span></div>
    <div class="contact">
      <h1 class="contact__name">DANIEL R. HAYES</h1>
      <p class="contact__title">Personal Financial Coach</p>
      <ul class="contact__list">
        <li class="contact__item">(205) 555-0187
          <svg class="contact__icon" viewBox="0 0 18 18"><rect x="4" y="1" width="10" height="16" rx="2" fill="none" stroke="var(--brand-green)" stroke-width="2"/><circle cx="9" cy="14" r="1.2" fill="var(--brand-green)"/></svg></li>
        <li class="contact__item">daniel@steadymoneypath.com
          <svg class="contact__icon" viewBox="0 0 18 18"><rect x="1" y="4" width="16" height="11" fill="var(--brand-green)"/><path d="M1,4 L9,10 L17,4" fill="none" stroke="var(--white)" stroke-width="1.4"/></svg></li>
        <li class="contact__item">www.steadymoneypath.com
          <svg class="contact__icon" viewBox="0 0 18 18"><circle cx="9" cy="9" r="8" fill="var(--brand-green)"/><path d="M1,9 H17 M9,1 C5,5 5,13 9,17 M9,1 C13,5 13,13 9,17" fill="none" stroke="var(--white)" stroke-width="1.2"/></svg></li>
      </ul>
    </div>
  </section>

  <section class="card card--back" aria-label="Card back">
    <div class="brand brand--back"><span class="brand__dot"></span><span class="brand__name">CLEARPATH<br>FINANCIAL COACHING</span></div>
    <div class="pitch">
      <h2 class="pitch__headline">STRUGGLING WITH YOUR FINANCES?</h2>
      <p class="pitch__line">Learn to become debt free<span class="pitch__bullet"></span>Discover the power of cash</p>
      <p class="pitch__line">Control your money instead of it controlling you</p>
      <p class="pitch__closing">Let us help you achieve a new level of financial freedom!</p>
      <div class="pitch__rule"></div>
      <p class="pitch__offer">SPECIAL OFFER!: FREE 30 minute consultation</p>
    </div>
  </section>

</main>
</body>
</html>
```